International Trade Consulting Firm Seeks Quality Newsletter Design

Our company provides consulting services to Pinnacle 300 type companies. We compete with the largest consulting companies in the world. However, we have the highest level of expertise in the industry and need to look the most professional and high end. We have very relevant and important information to provide our customers about their compliance and projects. We will have the winning design coded to be an e-newsletter, so it needs to be one page. We want to keep our company colors and logo design in the newsletter, they are attached. We DO NOT want it to look like a mini-version of our website. We want a fresh look to this marketing piece. Newsletter will need to include title, possible sub-heading, space for a feature story, 2 other stories included, and space on either the left or right for short cuts, links or highlights of other articles. Contents/'In this issue' section, about us or branding area, section for relevant links, etc...
Pinnacle 300 companies, High-level management
Marketing

```html
<!DOCTYPE html>
<html lang="en">
<head>
<meta charset="utf-8">
<title>Meridian Trade Advisors Newsletter</title>
<link href="https://fonts.googleapis.com/css2?family=Cinzel:wght@400;700&family=Questrial&family=Montserrat:wght@700;800&family=Arimo:wght@700&display=swap" rel="stylesheet">
<style>
  :root {
    --green-deep: #0c2a12;
    --green-dark: #143d1a;
    --green-mid: #2f7d2a;
    --green-bright: #6fc63a;
    --green-lime: #8ed645;
    --gold: #d9c98a;
    --ink: #333333;
    --ink-soft: #4d4d4d;
    --blue-link: #2a3aa8;
    --footer: #4a4a4a;
    --paper: #ffffff;
    --paper-shade: #e9e9e9;
  }
  * { box-sizing: border-box; margin: 0; padding: 0; }
  html, body { width: 770px; height: 1200px; overflow: hidden; background: #f0f0f0; }
  .newsletter {
    position: relative; width: 770px; height: 1200px; overflow: hidden;
    background: linear-gradient(180deg, var(--paper) 0%, var(--paper) 60%, var(--paper-shade) 100%);
    font-family: "Questrial", sans-serif; color: var(--ink);
  }
  .masthead {
    position: absolute; left: 0; top: 0; width: 770px; height: 323px;
    background:
      radial-gradient(ellipse at 92% 15%, rgba(170,240,110,.75) 0%, rgba(90,170,50,.4) 25%, transparent 55%),
      linear-gradient(90deg, var(--green-deep) 0%, var(--green-dark) 45%, var(--green-mid) 80%, #58a83a 100%);
  }
  .issue-label {
    position: absolute; left: 82px; top: 30px;
    font-family: "Cinzel", serif; font-weight: 400; font-size: 44px; letter-spacing: 1px;
    color: var(--gold); line-height: 1;
  }
  .main-title {
    position: absolute; left: 36px; top: 78px;
    font-family: "Montserrat", sans-serif; font-weight: 700; font-size: 52px; letter-spacing: 6px;
    color: #ffffff; line-height: 1;
  }
  .sub-title {
    position: absolute; left: 72px; top: 136px;
    font-family: "Cinzel", serif; font-weight: 700; font-size: 28px; letter-spacing: 18px;
    color: var(--gold); line-height: 1;
  }
  .brand-plate {
    position: absolute; left: 459px; top: 40px; width: 277px; height: 112px;
    background: #050505;
    display: flex; align-items: center; justify-content: center; text-align: center;
  }
  .brand-name {
    font-family: "Montserrat", sans-serif; font-weight: 800; font-size: 25px; line-height: 1.15;
    letter-spacing: 2px; color: var(--green-bright); text-transform: uppercase;
  }
  .hero {
    position: absolute; left: 35px; top: 176px; width: 699px; height: 322px;
    border: 4px solid #3fb235;
    background: linear-gradient(120deg, #e9eef2 0%, #c9d3da 35%, #2a3140 60%, #d8dee3 100%);
  }
  .lead {
    position: absolute; left: 0; top: 512px; width: 770px; text-align: center;
    font-family: "Cinzel", serif; font-weight: 400; font-size: 21px; line-height: 23px;
    color: var(--ink-soft);
  }
  .story-heading {
    position: absolute; top: 604px; width: 167px; height: 30px;
    background: linear-gradient(180deg, var(--green-lime) 0%, #54b22f 100%);
    font-family: "Arimo", sans-serif; font-weight: 700; font-size: 18px; line-height: 30px;
    color: var(--blue-link); text-align: center;
  }
  .story {
    position: absolute; top: 644px; width: 219px;
    font-size: 12px; line-height: 13.6px; text-align: justify; color: var(--ink);
  }
  .story p + p { margin-top: 14px; }
  .col-1 { left: 28px; }
  .col-2 { left: 274px; }
  .col-3 { left: 520px; }
  .h-1 { left: 56px; }
  .h-2 { left: 301px; }
  .h-3 { left: 547px; }
  .link-row { position: absolute; top: 1099px; left: 0; width: 770px; height: 24px; }
  .link-cta {
    position: absolute; left: 226px; top: 2px;
    font-size: 16px; color: #3b9a2e;
  }
  .link-box {
    position: absolute; left: 306px; top: 0; width: 434px; height: 24px;
    background: linear-gradient(180deg, var(--green-lime) 0%, #5cbc30 100%);
    font-family: "Arimo", sans-serif; font-weight: 700; font-size: 11.5px; line-height: 24px;
    color: var(--blue-link); padding-left: 14px; white-space: nowrap;
  }
  .link-box svg { vertical-align: -2px; margin-right: 3px; }
  .rule { position: absolute; left: 0; top: 1136px; width: 770px; height: 3px; background: #3fb235; }
  .footer {
    position: absolute; left: 0; top: 1144px; width: 770px; height: 56px;
    background: linear-gradient(180deg, #5a5a5a 0%, var(--footer) 100%); color: #ffffff;
  }
  .footer-brand {
    position: absolute; left: 44px; top: 1120px; width: 104px; height: 42px; background: #050505;
    display: flex; align-items: center; justify-content: center; text-align: center;
    font-family: "Montserrat", sans-serif; font-weight: 800; font-size: 9px; line-height: 1.15;
    color: var(--green-bright); text-transform: uppercase; letter-spacing: .5px;
  }
  .contact { position: absolute; font-size: 12.5px; white-space: nowrap; }
  .contact svg { vertical-align: -2px; margin-right: 3px; }
  .address { left: 44px; top: 28px; }
  .email { left: 380px; top: 7px; }
  .web { left: 380px; top: 28px; letter-spacing: 2px; font-family: "Arimo", sans-serif; font-weight: 700; font-size: 11.5px; }
  .phone { left: 568px; top: 20px; font-family: "Arimo", sans-serif; font-weight: 700; font-size: 21px; }
  .phone svg { vertical-align: -3px; }
</style>
</head>
<body>
<main class="newsletter">
  <header class="masthead">
    <div class="issue-label">NEWSLETTER</div>
    <h1 class="main-title">MAIN TITLE</h1>
    <div class="sub-title">SUB TITLE</div>
    <div class="brand-plate"><span class="brand-name">Meridian Trade<br>Advisors</span></div>
  </header>

  <div class="hero" role="img" aria-label="Photograph of four business consultants meeting around a table with a tablet and report"></div>

  <p class="lead">The Meridian Trade Advisors<br>offers the strongest team of experienced trade<br>consultants available anywhere</p>

  <h2 class="story-heading h-1">Feature story</h2>
  <h2 class="story-heading h-2">Other story1</h2>
  <h2 class="story-heading h-3">Other story2</h2>

  <article class="story col-1">
    <p>Lorem ipsum dolor sit amet, consectetuer adipiscing elit, sed diam nonummy nibh euismod tincidunt ut laoreet dolore magna aliquam erat volutpat. Ut wisi enim ad minim veniam, quis nostrud exerci tation ullamcorper suscipit lobortis nisl ut aliquip ex ea commodo consequat. Duis autem vel eum iriure dolor in hendrerit in vulputate velit esse molestie consequat, vel illum dolore eu feugiat nulla facilisis at vero eros et accumsan et iusto odio dignissim qui blandit praesent luptatum zzril delenit augue duis dolore te feugait nulla facilisi.</p>
    <p>Lorem ipsum dolor sit amet, consectetuer adipiscing elit, sed diam nonummy nibh euismod tincidunt ut laoreet dolore magna aliquam erat volutpat. Ut wisi enim ad minim veniam, quis nostrud exerci tation ullamcorper suscipit lobortis nisl ut aliquip ex ea commodo consequat. Duis autem vel eum iriure dolor in hendrerit in vulputate velit esse molestie consequat, vel illum dolore eu feugiat nulla facilisis at vero eros et accumsan.</p>
  </article>
  <article class="story col-2">
    <p>Lorem ipsum dolor sit amet, consectetuer adipiscing elit, sed diam nonummy nibh euismod tincidunt ut laoreet dolore magna aliquam erat volutpat. Ut wisi enim ad minim veniam, quis nostrud exerci tation ullamcorper suscipit lobortis nisl ut aliquip ex ea commodo consequat. Duis autem vel eum iriure dolor in hendrerit in vulputate velit esse molestie consequat, vel illum dolore eu feugiat nulla facilisis at vero eros et accumsan et iusto odio dignissim qui blandit praesent luptatum zzril delenit augue duis dolore te feugait nulla facilisi.</p>
    <p>Lorem ipsum dolor sit amet, consectetuer adipiscing elit, sed diam nonummy nibh euismod tincidunt ut laoreet dolore magna aliquam erat volutpat. Ut wisi enim ad minim veniam, quis nostrud exerci tation ullamcorper suscipit lobortis nisl ut aliquip ex ea commodo consequat. Duis autem vel eum iriure dolor in hendrerit in vulputate velit esse molestie consequat, vel illum dolore eu feugiat nulla facilisis at vero eros et accumsan.</p>
  </article>
  <article class="story col-3">
    <p>Lorem ipsum dolor sit amet, consectetuer adipiscing elit, sed diam nonummy nibh euismod tincidunt ut laoreet dolore magna aliquam erat volutpat. Ut wisi enim ad minim veniam, quis nostrud exerci tation ullamcorper suscipit lobortis nisl ut aliquip ex ea commodo consequat. Duis autem vel eum iriure dolor in hendrerit in vulputate velit esse molestie consequat, vel illum dolore eu feugiat nulla facilisis at vero eros et accumsan et iusto odio dignissim qui blandit praesent luptatum zzril delenit augue duis dolore te feugait nulla facilisi.</p>
    <p>Lorem ipsum dolor sit amet, consectetuer adipiscing elit, sed diam nonummy nibh euismod tincidunt ut laoreet dolore magna aliquam erat volutpat. Ut wisi enim ad minim veniam, quis nostrud exerci tation ullamcorper suscipit lobortis nisl ut aliquip ex ea commodo consequat. Duis autem vel eum iriure dolor in hendrerit in vulputate velit esse molestie consequat, vel illum dolore eu feugiat nulla facilisis at vero eros et accumsan.</p>
  </article>

  <div class="link-row">
    <span class="link-cta">click here</span>
    <span class="link-box"><svg width="12" height="12" viewBox="0 0 12 12" fill="none" stroke="#2a3aa8" stroke-width="1.2"><circle cx="6" cy="6" r="5"/><ellipse cx="6" cy="6" rx="2.2" ry="5"/><line x1="1" y1="6" x2="11" y2="6"/></svg>www.meridiantrade.com/news/issue-briefing-quarterly1111</span>
  </div>

  <div class="rule"></div>
  <footer class="footer">
    <span class="contact address"><svg width="10" height="13" viewBox="0 0 10 13"><path d="M5 0C2.2 0 0 2.2 0 5c0 3.5 5 8 5 8s5-4.5 5-8C10 2.2 7.8 0 5 0zm0 7a2 2 0 1 1 0-4 2 2 0 0 1 0 4z" fill="#fff"/></svg>418 Harbor Line Drive, Bayport, Florida 32901</span>
    <span class="contact email"><svg width="14" height="10" viewBox="0 0 14 10" fill="none" stroke="#fff" stroke-width="1.2"><rect x=".6" y=".6" width="12.8" height="8.8"/><path d="M.6.6 7 5.6 13.4.6"/></svg>info@meridiantrade.com</span>
    <span class="contact web"><svg width="12" height="12" viewBox="0 0 12 12" fill="none" stroke="#fff" stroke-width="1.2"><circle cx="6" cy="6" r="5"/><ellipse cx="6" cy="6" rx="2.2" ry="5"/><line x1="1" y1="6" x2="11" y2="6"/></svg>www.meridiantrade.com</span>
    <span class="contact phone"><svg width="20" height="20" viewBox="0 0 20 20" fill="none" stroke="#fff" stroke-width="1.5"><circle cx="10" cy="10" r="9"/><path d="M7 5.5c-1.5 1-1.5 3 0 5.5s3.5 4 5 3.5l1-1.5-2-1.5-1 .8c-1-.5-2-1.8-2.4-2.8l.9-.9-1-2.2z" fill="#fff" stroke="none"/></svg> 555.014.2290</span>
  </footer>
  <div class="footer-brand">Meridian Trade<br>Advisors</div>
</main>
</body>
</html>
```